TV Antenna Installation business needs a unique flyer

We need a simple but effective flyer design for our TV Aerial installation company based in Newcastle, NSW, Australia called Bright Harbour TV & Aerial Svcs.
We are trying to target areas where there has been a new transmitter installed and most houses just require their aerial redirecting and tv's retuning.

Industry/Entity Type

Business

Requirements
Must have
• We would like the idea of a headline phrase such as " Poor TV reception……..now a thing from the past" or something similar & catchy.
Also "Did you know a new transmitter has been recently installed in your area, we can therefore now GUARANTEE 100% PERFECT PICTURE
Charges from only $95.
- Free 5 year warranty
- Free signal testing
- Free Onsite Quote
Phone 0463 527 209
Nice to have
• Other services include:

- New Installs
- Extra Points & repairs
- TV wall mounting/Home Cinema
- Pull down tall masts

Modern tv picture, see example uploaded

```html
<!DOCTYPE html>
<html lang="en">
<head>
<meta charset="utf-8">
<title>Bright Harbour TV &amp; Aerial Svcs – Flyer</title>
<link href="https://fonts.googleapis.com/css2?family=Roboto:wght@700;900&family=Roboto+Condensed:wght@700&family=PT+Sans+Narrow:wght@400;700&display=swap" rel="stylesheet">
<style>
  :root {
    --backdrop: #e6e6e6;
    --white: #ffffff;
    --brand-blue: #0c5aa8;
    --navy: #123f78;
    --red: #e4262b;
    --red-light: #f05a5e;
    --lime: #c9d52c;
    --lime-light: #eceb78;
    --ink: #2b2a1c;
    --gold: #ffe21a;
    --tv-yellow: #f2e23a;
    --tv-yellow-dark: #c9b51c;
    --bar-blue: #1c5fa0;
    --bar-blue-dark: #0f3f76;
  }
  * { margin: 0; padding: 0; box-sizing: border-box; }
  html, body { width: 923px; height: 1200px; overflow: hidden; }
  body { background: var(--backdrop); position: relative; font-family: "PT Sans Narrow", "Arial Narrow", sans-serif; }

  .flyer { position: absolute; left: 39px; top: 0; width: 845px; height: 1200px; overflow: hidden; background: linear-gradient(100deg, var(--lime) 0%, var(--lime-light) 100%); }

  .header { position: absolute; left: 0; top: 0; width: 100%; height: 219px; background: var(--white); }
  .business-name { position: absolute; left: 0; right: 0; top: 38px; text-align: center; font-family: "Roboto", Arial, sans-serif; font-weight: 700; font-size: 63px; line-height: 80px; color: var(--brand-blue); letter-spacing: -0.5px; transform: scaleX(0.92); }

  .hero { position: absolute; left: 0; top: 219px; width: 100%; height: 326px; background: linear-gradient(90deg, var(--red) 0%, var(--red) 55%, var(--red-light) 100%); }
  .location-tab { position: absolute; left: 218px; top: 205px; width: 396px; height: 46px; background: var(--white); border-radius: 0 0 14px 14px; text-align: center; font-family: "Roboto", Arial, sans-serif; font-weight: 700; font-size: 23px; line-height: 46px; color: var(--ink); }

  .headline { position: absolute; left: 39px; top: 268px; font-weight: 700; font-size: 46px; line-height: 62px; color: var(--white); }
  .hero-copy { position: absolute; left: 39px; top: 410px; width: 470px; font-size: 16px; line-height: 28px; color: var(--white); text-align: justify; }

  .tv-illustration { position: absolute; left: 556px; top: 292px; width: 248px; height: 350px; border-radius: 28px; background: linear-gradient(160deg, var(--tv-yellow) 0%, #f7ec74 45%, var(--tv-yellow-dark) 100%); }

  .price-badge { position: absolute; left: 61px; top: 530px; width: 404px; height: 72px; }
  .price-badge .tab { position: absolute; left: -8px; top: -8px; width: 404px; height: 20px; background: var(--navy); transform: skewX(-10deg); }
  .price-badge .face { position: absolute; inset: 0; background: linear-gradient(180deg, #2f7fcc, #15508f); border-radius: 4px; box-shadow: 0 4px 8px rgba(0,0,0,0.3); text-align: center; font-weight: 700; font-size: 37px; line-height: 72px; color: var(--white); }

  .phone-line { position: absolute; left: 40px; top: 624px; display: flex; align-items: center; gap: 12px; color: var(--ink); font-family: "Roboto Condensed", "Arial Narrow", sans-serif; font-weight: 700; }
  .phone-line .label { font-size: 40px; }
  .phone-line .number { font-size: 56px; }
  .phone-icon { width: 58px; height: 58px; margin-left: 6px; }

  .interior-photo { position: absolute; left: 50px; top: 706px; width: 363px; height: 164px; border-radius: 14px; border: 5px solid var(--white); background: linear-gradient(120deg, #d8c6a2 0%, #a9906a 55%, #5a4838 100%); box-shadow: 0 4px 10px rgba(0,0,0,0.3); }

  .services { position: absolute; left: 498px; top: 748px; }
  .services h2 { font-weight: 700; font-size: 29px; color: var(--brand-blue); margin-bottom: 12px; }
  .services ul { list-style: none; }
  .services li { position: relative; padding-left: 36px; font-size: 23px; line-height: 29px; margin-bottom: 8px; color: var(--ink); }
  .services li::before { content: ""; position: absolute; left: 8px; top: 7px; width: 16px; height: 16px; border-radius: 50%; background: radial-gradient(circle at 35% 35%, #ff6b6b, #c4161c); }

  .guarantee-box { position: absolute; left: 53px; top: 896px; width: 343px; height: 284px; background: linear-gradient(180deg, #ee3b3f, #d8262a); box-shadow: 0 4px 10px rgba(0,0,0,0.3); text-align: center; padding-top: 22px; color: var(--white); }
  .guarantee-box p { font-weight: 700; font-size: 25px; line-height: 32px; }
  .guarantee-box .guarantee { margin-top: 14px; font-family: "Roboto", Arial, sans-serif; font-weight: 900; font-size: 35px; line-height: 42px; color: var(--gold); }

  .freebies { position: absolute; left: 396px; top: 998px; width: 375px; }
  .freebies li { list-style: none; height: 50px; margin-bottom: 3px; padding-left: 50px; font-weight: 700; font-size: 29px; line-height: 50px; color: var(--white); background: linear-gradient(180deg, var(--bar-blue), var(--bar-blue-dark)); box-shadow: 0 3px 6px rgba(0,0,0,0.25); }
</style>
</head>
<body>
  <main class="flyer">
    <header class="header">
      <h1 class="business-name">Bright Harbour TV &amp;<br>Aerial Svcs</h1>
    </header>

    <section class="hero"></section>
    <div class="location-tab">Newcastle, NSW, Australia</div>

    <h2 class="headline">Poor TV Reception?<br>Now a thing from the Past</h2>
    <p class="hero-copy">We are trying to target areas where there has been a new transmitter installed and most houses just require their aerial redirecting and tv's retuning.</p>

    <div class="tv-illustration" role="img" aria-label="Illustration of a yellow retro television set with antennas"></div>

    <div class="price-badge">
      <div class="tab"></div>
      <div class="face">Charges from only $95</div>
    </div>

    <div class="phone-line">
      <span class="label">Call:</span>
      <span class="number">0463 527 209</span>
      <svg class="phone-icon" viewBox="0 0 24 24" aria-hidden="true">
        <path fill="#111" d="M6.62 10.79c1.44 2.83 3.76 5.14 6.59 6.59l2.2-2.2c.27-.27.67-.36 1.02-.24 1.12.37 2.33.57 3.57.57.55 0 1 .45 1 1V20c0 .55-.45 1-1 1-9.39 0-17-7.61-17-17 0-.55.45-1 1-1h3.5c.55 0 1 .45 1 1 0 1.25.2 2.45.57 3.57.11.35.03.74-.25 1.02l-2.2 2.2z"/>
      </svg>
    </div>

    <div class="interior-photo" role="img" aria-label="Photo of a modern living room with a wall-mounted flat screen TV"></div>

    <section class="services">
      <h2>OUR OTHER SERVICES:</h2>
      <ul>
        <li>New Installs</li>
        <li>Extra Points &amp; repairs</li>
        <li>TV wall mounting/<br>Home Cinema</li>
        <li>Pull down tall masts</li>
      </ul>
    </section>

    <section class="guarantee-box">
      <p>Did you know a new<br>transmitter has been recently<br>installed in your area,<br>we can therefore NOW</p>
      <p class="guarantee">GUARANTEE 100%<br>PERFECT PICTURE</p>
    </section>

    <ul class="freebies">
      <li>Free 5 Year Warranty</li>
      <li>Free Signal Testing</li>
      <li>Free Onsite Quote</li>
    </ul>
  </main>
</body>
</html>
```